Plate of the Raven: Half-Page Magazine Ad

advertisement in a travel magazine for a casual/fine dining restaurant in the heart of Whitehorse, Yukon
Needs to say that it is located in the Stonefield Hotel, 247 Larch Avenue.

Northern inspired cuisine
plateoftheraven.example

Don't need to use all the pictures

Dimensions: ad is a half-page, dimensions are 7.25" x 4.8".

Target Market(s)

Upscale dining, corporate travellers

Industry/Entity Type

Restaurant

Colors
0054AA
0677BA
7BADD7
CADEEF
E8F1F8
0094D4
00A9DD
6FCCEA
C7EBF8
E9F6FB
00AB8E
00BBA5
67D7C9
C6EFE9
E9F9F6

Requirements
Must have
• Restaurant logo
Nice to have
• Simple, clean design with upscale feel

```html
<!DOCTYPE html>
<html lang="en">
<head>
<meta charset="utf-8">
<title>Plate of the Raven – Half-Page Ad</title>
<link rel="stylesheet" href="https://fonts.googleapis.com/css2?family=Poppins:wght@300;400;600;700;800&display=swap">
<style>
  :root {
    --page-bg: #ffffff;
    --ink: #0b0b0b;
    --ink-soft: #2a2a2a;
    --grey-text: #7a7a7a;
    --grey-mid: #9a9a9a;
    --ring-light: #e3e3e3;
    --sketch-light: #f1f1f1;
    --sketch-dark: #a9a9a9;
    --patio-light: #f4f4f4;
    --patio-dark: #d6d6d6;
    --badge-top: #2b2b2b;
    --badge-bottom: #000000;
    --badge-text: #ffffff;
    --badge-text-soft: #d0d0d0;
    --food-warm: #e07a2a;
    --food-deep: #b5461c;
    --food-green: #5d8a36;
    --bowl-rim: #3c3c3c;
    --photo-sky: #cfdbe3;
    --photo-wall: #6b6e73;
    --photo-flowers: #5b3a8c;
  }
  * { margin: 0; padding: 0; box-sizing: border-box; }
  html, body { width: 1200px; height: 2400px; overflow: hidden; background: var(--page-bg); }
  .canvas { position: relative; width: 1200px; height: 2400px; background: var(--page-bg); }
  .ad {
    position: absolute; left: 60px; top: 435px;
    width: 930px; height: 1318px;
    transform: scale(1.1613); transform-origin: 0 0;
    background: var(--page-bg); overflow: hidden;
    font-family: "Poppins", sans-serif; color: var(--ink);
    box-shadow: 0 6px 26px rgba(0,0,0,0.28);
  }
  .patio-backdrop {
    position: absolute; left: 0; top: 620px; width: 640px; height: 698px;
    background: linear-gradient(160deg, var(--patio-light) 0%, var(--patio-dark) 100%);
    opacity: 0.7;
  }
  .bison-sketch {
    position: absolute; left: 0; top: 0; width: 470px; height: 650px;
    background: radial-gradient(ellipse at 55% 50%, var(--sketch-dark) 0%, #cfcfcf 45%, var(--sketch-light) 80%, var(--page-bg) 100%);
  }
  .brand-name {
    position: absolute; left: 518px; top: 92px; width: 300px;
    font-weight: 800; color: var(--ink); line-height: 0.95; letter-spacing: -2px;
  }
  .brand-name span { display: block; }
  .brand-name .big { font-size: 82px; }
  .brand-name .small { font-size: 64px; margin: 10px 0; }
  .headline { position: absolute; left: 68px; top: 610px; line-height: 56px; font-size: 55px; }
  .headline .strong { font-weight: 700; display: block; }
  .headline .light { font-weight: 300; display: block; line-height: 58px; }
  .hours { position: absolute; left: 70px; top: 976px; font-size: 30px; line-height: 31px; font-weight: 700; color: var(--grey-text); }
  .location { position: absolute; left: 66px; top: 1088px; width: 310px; height: 100px; }
  .location svg { position: absolute; left: 0; top: 0; }
  .location .label { position: absolute; left: 22px; top: 0; font-size: 17px; font-weight: 400; color: var(--grey-mid); }
  .location .venue { position: absolute; left: 4px; top: 26px; font-size: 26px; font-weight: 700; color: var(--ink-soft); white-space: nowrap; }
  .location .street { position: absolute; left: 4px; top: 58px; font-size: 25px; font-weight: 300; letter-spacing: 3.5px; color: var(--ink-soft); white-space: nowrap; }
  .website { position: absolute; left: 70px; top: 1212px; font-size: 17px; font-weight: 700; letter-spacing: 0.6px; color: var(--ink-soft); }
  .patio-ring { position: absolute; left: 492px; top: 562px; }
  .patio-photo {
    position: absolute; left: 520px; top: 592px; width: 370px; height: 370px; border-radius: 50%;
    background: linear-gradient(110deg, var(--photo-wall) 0%, var(--photo-sky) 45%, var(--photo-wall) 60%, var(--photo-flowers) 100%);
  }
  .food-bowl {
    position: absolute; left: 386px; top: 930px; width: 620px; height: 620px; border-radius: 50%;
    border: 14px solid var(--bowl-rim);
    background: radial-gradient(circle at 50% 45%, var(--food-warm) 0%, var(--food-deep) 45%, var(--food-green) 75%, var(--food-deep) 100%);
  }
  .cuisine-badge { position: absolute; left: 427px; top: 848px; }
  .cuisine-badge-text {
    position: absolute; left: 437px; top: 918px; width: 226px; text-align: center;
    font-weight: 700; font-size: 28px; line-height: 30px; color: var(--badge-text);
  }
  .cuisine-badge-text .soft { color: var(--badge-text-soft); font-size: 33px; }
</style>
</head>
<body>
<div class="canvas">
  <article class="ad">
    <div class="patio-backdrop" role="img" aria-label="Faded black and white photo of the restaurant patio"></div>
    <div class="bison-sketch" role="img" aria-label="Pencil sketch of a raven, restaurant illustration"></div>

    <h1 class="brand-name"><span class="big">PLATE</span><span class="small">OF THE</span><span class="big">RAVEN</span></h1>

    <h2 class="headline">
      <span class="strong">A FINE</span>
      <span class="strong">DINING</span>
      <span class="strong">RESTAURANT</span>
      <span class="light">IN THE HEART OF</span>
      <span class="light">WHITEHORSE,</span>
      <span class="light">YUKON</span>
    </h2>

    <p class="hours">OPEN EVENINGS WITH<br>A SUMMER PATIO</p>

    <div class="location">
      <svg width="310" height="100" viewBox="0 0 310 100">
        <path d="M9 2 a7 7 0 0 1 7 7 c0 5 -7 12 -7 12 s-7 -7 -7 -12 a7 7 0 0 1 7 -7z" fill="none" stroke="#7a7a7a" stroke-width="2"/>
        <circle cx="9" cy="9" r="2.5" fill="#7a7a7a"/>
        <path d="M120 12 H296 a6 6 0 0 1 6 6 V80 a6 6 0 0 1 -6 6 H240" fill="none" stroke="#8a8a8a" stroke-width="1.3" stroke-dasharray="4 3"/>
        <path d="M4 88 V96" stroke="#8a8a8a" stroke-width="1.3" stroke-dasharray="2 2"/>
      </svg>
      <span class="label">Located In</span>
      <span class="venue">STONEFIELD HOTEL</span>
      <span class="street">247 LARCH AVENUE</span>
    </div>

    <p class="website">www.plateoftheraven.example</p>

    <svg class="patio-ring" width="426" height="426" viewBox="0 0 426 426">
      <circle cx="213" cy="213" r="213" fill="var(--ring-light)"/>
    </svg>
    <div class="patio-photo" role="img" aria-label="Photo of the hotel patio with tables and purple flower planters"></div>

    <div class="food-bowl" role="img" aria-label="Photo of a bowl of pappardelle pasta with ragu, shaved parmesan and microgreens"></div>

    <svg class="cuisine-badge" width="246" height="246" viewBox="0 0 246 246">
      <defs>
        <linearGradient id="badgeFill" x1="0" y1="0" x2="0" y2="1">
          <stop offset="0" stop-color="var(--badge-top)"/>
          <stop offset="1" stop-color="var(--badge-bottom)"/>
        </linearGradient>
      </defs>
      <circle cx="123" cy="123" r="123" fill="#ffffff"/>
      <circle cx="123" cy="123" r="110" fill="url(#badgeFill)"/>
    </svg>
    <p class="cuisine-badge-text">NORTHERN<br>INSPIRED<br><span class="soft">CUISINE</span></p>
  </article>
</div>
</body>
</html>
```